Car transport business

We need a new business card design. Attached is our old card sample. I would just like to adjust the logo colors (blue and red) to be brighter. I changed my name to the brighter red and the word dispatcher to a brighter blue as an example. But you can adjust those colors further. And then perhaps you can use the same colors for the card design but use your imagination.

As a suggestion so the card stands out I would like to add a clip art of car carrier truck. Attached are examples of that as well

```html
<!DOCTYPE html>
<html lang="en">
<head>
<meta charset="utf-8">
<title>Northlane Business Card</title>
<link rel="stylesheet" href="https://fonts.googleapis.com/css2?family=Exo+2:wght@700&family=Montserrat:wght@400;500;800&display=swap">
<style>
  :root {
    --page-bg: #e9e6e2;
    --navy: #0c2a5c;
    --blue: #1f57a8;
    --blue-light: #3a78c4;
    --red: #d9161f;
    --frost: #dfe3e8;
    --frost-dark: #c3cad3;
    --text-light: #e6e9ee;
    --text-muted: #d3d9e2;
    --logo-navy: #14306b;
  }
  * { margin: 0; padding: 0; box-sizing: border-box; }
  html, body { width: 1200px; height: 969px; overflow: hidden; background: var(--page-bg); }
  .card {
    position: absolute; left: 100px; top: 200px;
    width: 1000px; height: 570px;
    border-radius: 28px; overflow: hidden;
    box-shadow: 0 10px 30px rgba(0,0,0,.18);
  }
  .card-art { position: absolute; inset: 0; }
  .contact-block { position: absolute; left: 66px; top: 58px; color: var(--text-light); }
  .person-name {
    font-family: "Exo 2", sans-serif; font-weight: 700;
    font-size: 34px; letter-spacing: 1px; color: var(--text-light);
  }
  .person-role {
    font-family: "Montserrat", sans-serif; font-weight: 500;
    font-size: 21px; color: var(--text-muted); margin-top: 2px;
  }
  .contact-list { list-style: none; margin-top: 34px; }
  .contact-list li {
    display: flex; align-items: center; gap: 10px;
    font-family: "Montserrat", sans-serif; font-size: 23px; line-height: 30px;
  }
  .contact-list svg { width: 20px; height: 20px; fill: var(--text-light); flex: none; }
  .social-row { display: flex; gap: 12px; margin-top: 26px; }
  .social-dot { width: 30px; height: 30px; border-radius: 50%; background: var(--text-light); }
  .brand-lockup { position: absolute; left: 555px; top: 428px; }
  .brand-mark { display: flex; align-items: center; gap: 12px; }
  .brand-circle { width: 44px; height: 44px; border-radius: 50%; background: var(--red); }
  .brand-name {
    font-family: "Montserrat", sans-serif; font-weight: 800;
    font-size: 42px; letter-spacing: 2px; color: var(--logo-navy);
  }
  .brand-tagline {
    margin: 6px 0 0 58px;
    font-family: "Montserrat", sans-serif; font-weight: 800;
    font-size: 12px; letter-spacing: 1.6px; color: var(--logo-navy);
    text-transform: uppercase; white-space: nowrap;
  }
</style>
</head>
<body>
  <div class="card">
    <svg class="card-art" viewBox="0 0 1000 570" width="1000" height="570">
      <defs>
        <linearGradient id="frostFill" x1="0" y1="0" x2="1" y2="1">
          <stop offset="0" stop-color="var(--frost)"/>
          <stop offset="1" stop-color="var(--frost-dark)"/>
        </linearGradient>
        <linearGradient id="blueFill" x1="0" y1="0" x2="1" y2="0.6">
          <stop offset="0" stop-color="var(--blue)"/>
          <stop offset="0.5" stop-color="var(--blue-light)"/>
          <stop offset="1" stop-color="var(--navy)"/>
        </linearGradient>
        <linearGradient id="truckFill" x1="0" y1="0" x2="0" y2="1">
          <stop offset="0" stop-color="#9aa3ad" stop-opacity="0.25"/>
          <stop offset="1" stop-color="#6b737c" stop-opacity="0.4"/>
        </linearGradient>
      </defs>
      <rect class="frost-panel" width="1000" height="570" fill="url(#frostFill)"/>
      <rect class="truck-illustration" x="600" y="236" width="400" height="334"
            fill="url(#truckFill)" role="img" aria-label="Faint drawing of a car carrier truck"/>
      <polygon class="blue-panel" points="0,0 1000,0 1000,70 250,570 0,570" fill="url(#blueFill)"/>
      <polygon class="red-band" points="1000,98 1000,122 318,570 282,570" fill="var(--red)"/>
    </svg>

    <div class="contact-block">
      <div class="person-name">DAN RIVERA</div>
      <div class="person-role">Dispatcher</div>
      <ul class="contact-list">
        <li><svg viewBox="0 0 24 24"><path d="M6.6 10.8a15.1 15.1 0 0 0 6.6 6.6l2.2-2.2a1 1 0 0 1 1-.25 11.4 11.4 0 0 0 3.6.57 1 1 0 0 1 1 1V20a1 1 0 0 1-1 1A17 17 0 0 1 3 4a1 1 0 0 1 1-1h3.5a1 1 0 0 1 1 1c0 1.25.2 2.45.57 3.57a1 1 0 0 1-.25 1z"/></svg>555-010-4821</li>
        <li><svg viewBox="0 0 24 24"><path d="M7 1h10a2 2 0 0 1 2 2v18a2 2 0 0 1-2 2H7a2 2 0 0 1-2-2V3a2 2 0 0 1 2-2zm0 3v14h10V4zm5 15.5a1 1 0 1 0 0 2 1 1 0 0 0 0-2z"/></svg>555-010-7396</li>
        <li><svg viewBox="0 0 24 24"><path d="M3 5h18v14H3zm2 2v.5l7 4.5 7-4.5V7zm0 2.9V17h14V9.9l-7 4.5z"/></svg>northlaneauto@mail.com</li>
        <li><svg viewBox="0 0 24 24"><path d="M12 2a10 10 0 1 0 0 20 10 10 0 0 0 0-20zm0 2a8 8 0 0 1 0 16 8 8 0 0 1 0-16z"/></svg>northlaneauto.com</li>
      </ul>
      <div class="social-row">
        <span class="social-dot"></span>
        <span class="social-dot"></span>
        <span class="social-dot"></span>
      </div>
    </div>

    <div class="brand-lockup">
      <div class="brand-mark">
        <span class="brand-circle"></span>
        <span class="brand-name">NORTHLANE</span>
      </div>
      <div class="brand-tagline">Reliable Vehicle Shipping Nationwide</div>
    </div>
  </div>
</body>
</html>
```